Brightwave Reach - Business Card

We need a business card for a Social Media Marketing company that specializes in online marketing for small businesses in Canada using common Social Media platforms such as Pixlora, Chatterly, Blinkpost & Quibber.

I have uploaded a copy of our logo which I would like utilized in the business card. We would like the business card to be modern yet classy design.

Our website is www.brightwavereach.ca

Industry/Entity Type

Marketing

Contact Information for Business Card

Email: info@brightwavereach.ca
Website: www.brightwavereach.ca
Telephone: 604-555-0193

Colors

Designer to choose colors to be used in the design.

Requirements
Must have
• Social Media icons on reverse
• Please add some designs with color.

```html
<!DOCTYPE html>
<html lang="en">
<head>
<meta charset="utf-8">
<title>Brightwave Reach – Business Card</title>
<link rel="stylesheet" href="https://fonts.googleapis.com/css2?family=Lato:wght@400;700;900&display=swap">
<style>
  :root {
    --stage: #2a2a2a;
    --card-dark: #3d4245;
    --card-light: #ffffff;
    --ink: #3a3d40;
    --brand-blue: #2a78bf;
    --white: #ffffff;
  }
  * { box-sizing: border-box; margin: 0; padding: 0; }
  html, body {
    width: 1200px; height: 1166px; overflow: hidden;
    background: var(--stage);
    font-family: "Lato", Arial, sans-serif;
  }
  .canvas {
    position: relative; width: 1200px; height: 1166px;
    display: flex; flex-direction: column; align-items: center;
    gap: 60px; padding-top: 50px;
  }
  .card {
    position: relative; width: 880px; height: 503px;
    overflow: hidden;
  }

  /* Wordmark */
  .wordmark {
    display: flex; align-items: center; gap: 18px;
  }
  .wordmark__mark { width: 30px; height: 30px; background: currentColor; flex: none; }
  .wordmark__name {
    font-weight: 900; font-size: 50px; letter-spacing: 1px;
    text-transform: uppercase; line-height: 1.05;
  }
  .wordmark__line { display: block; }

  /* Reverse side */
  .card--back { background: var(--card-dark); }
  .card--back .wordmark {
    position: absolute; left: 0; right: 0; top: 110px;
    justify-content: center;
    color: var(--white);
  }
  .social-row {
    position: absolute; left: 0; right: 0; bottom: 90px;
    display: flex; justify-content: center; gap: 56px;
    list-style: none;
  }
  .social-row__item {
    display: flex; align-items: center; gap: 10px;
    color: var(--white); font-size: 20px; font-weight: 700;
  }
  .social-row__tile {
    width: 40px; height: 40px; border-radius: 6px;
    background: var(--white);
  }

  /* Front side */
  .card--front { background: var(--card-light); }
  .card--front .wordmark {
    position: absolute; left: 70px; top: 185px;
    color: var(--ink);
  }
  .card--front .wordmark__mark { width: 26px; height: 26px; }
  .card--front .wordmark__name { font-size: 44px; }
  .contact {
    position: absolute; left: 500px; top: 150px;
  }
  .contact__name {
    color: var(--brand-blue); font-weight: 700; font-size: 28px;
    text-transform: uppercase; letter-spacing: 0.5px;
  }
  .contact__role {
    color: var(--ink); font-size: 22px; margin: 4px 0 20px 8px;
  }
  .contact__list { list-style: none; }
  .contact__line {
    display: flex; align-items: center; gap: 16px;
    color: var(--ink); font-size: 22px; line-height: 1.55;
    margin-left: 8px;
  }
  .contact__icon { width: 20px; height: 20px; flex: none; fill: var(--brand-blue); }
  .edge-band {
    position: absolute; left: 0; right: 0; bottom: 0; height: 14px;
    background: var(--brand-blue);
  }
</style>
</head>
<body>
<main class="canvas">
  <section class="card card--back" aria-label="Card reverse">
    <div class="wordmark">
      <span class="wordmark__mark"></span>
      <span class="wordmark__name"><span class="wordmark__line">Brightwave</span><span class="wordmark__line">Reach</span></span>
    </div>
    <ul class="social-row">
      <li class="social-row__item"><span class="social-row__tile"></span>Chatterly</li>
      <li class="social-row__item"><span class="social-row__tile"></span>Pixlora</li>
      <li class="social-row__item"><span class="social-row__tile"></span>Quibber</li>
      <li class="social-row__item"><span class="social-row__tile"></span>Blinkpost</li>
    </ul>
  </section>

  <section class="card card--front" aria-label="Card front">
    <div class="wordmark">
      <span class="wordmark__mark"></span>
      <span class="wordmark__name"><span class="wordmark__line">Brightwave</span><span class="wordmark__line">Reach</span></span>
    </div>
    <div class="contact">
      <h1 class="contact__name">Daniel Hartwell</h1>
      <p class="contact__role">Manager</p>
      <ul class="contact__list">
        <li class="contact__line">
          <svg class="contact__icon" viewBox="0 0 20 20" aria-hidden="true"><path d="M4 1.5l3 3.5-1.6 2.2c1 2.3 3 4.3 5.4 5.4L13 11l3.5 3-1.5 3.3C8 17 3 12 2.7 4.5z"/></svg>
          604-555-0193
        </li>
        <li class="contact__line">
          <svg class="contact__icon" viewBox="0 0 20 20" aria-hidden="true"><path d="M1 4h18v12H1z M2.5 5.5L10 11l7.5-5.5" fill="none" stroke="#2a78bf" stroke-width="1.8"/></svg>
          info@brightwavereach.ca
        </li>
        <li class="contact__line">
          <svg class="contact__icon" viewBox="0 0 20 20" aria-hidden="true"><g fill="none" stroke="#2a78bf" stroke-width="1.6"><circle cx="10" cy="10" r="8.2"/><ellipse cx="10" cy="10" rx="3.6" ry="8.2"/><path d="M2 10h16M3.5 5.5h13M3.5 14.5h13"/></g></svg>
          www.brightwavereach.ca
        </li>
      </ul>
    </div>
    <div class="edge-band"></div>
  </section>
</main>
</body>
</html>
```